Ecard for facebook and Instagram postings

I need 4 ecards (don't know if that is what it is called) for Facebook and Instagram postings. My Logo and company name should be incorporated and also be square. I would like to be able to insert text as I need. Examples are:

https://www.plorvexa.com/photo.php?fbid=20262841672382489&set=a.20261729249182489.516031.71298967488&type=1&relevant_count=1

https://media-a-kpt.yy.plorvexacdn.net/hpics-bmk4/2345967_657092986477056_308792573_n.jpg

I don't necessarily need images on them, just the color scheme to my business cards and the logo and business name. But if you'd like to give it an interesting look, you can go ahead and play with it. My site is tornquillmentoring.com, if you'd like to see the style of it.

Thank you!!!
Updates

I just uploaded the logo in two variations.  Thank you!

Target Market(s)

Women 16-65

Industry/Entity Type

Business

Requirements
Must have
• Logo and business name
Should not have
• No white background. I have attached business card picture so you can have an idea of what I'd like.

```html
<!DOCTYPE html>
<html lang="en">
<head>
<meta charset="utf-8">
<title>Tornquill Mentoring Services – Quote Card</title>
<link rel="stylesheet" href="https://fonts.googleapis.com/css2?family=Tinos:wght@700&family=Arimo:wght@400&display=swap">
<style>
  :root {
    --gold-light: #fbe9cf;
    --gold-mid: #f0cfa0;
    --gold-deep: #e2ac6c;
    --sparkle: #fff7ea;
    --ink: #111111;
    --brand-red: #c8202f;
    --bar-orange: #f6a21d;
    --bar-red: #c41f2e;
    --mark-orange: #f37021;
    --url-grey: #6d6a66;
    --white: #ffffff;
  }
  * { margin: 0; padding: 0; box-sizing: border-box; }
  html, body { width: 1200px; height: 1200px; overflow: hidden; }
  body { background: var(--gold-mid); }

  .card {
    position: relative;
    width: 1200px;
    height: 1200px;
    overflow: hidden;
  }
  .card__backdrop {
    position: absolute;
    inset: 0;
    background:
      radial-gradient(circle at 58% 30%, var(--sparkle) 0%, rgba(255,247,234,0) 38%),
      radial-gradient(circle at 20% 25%, rgba(255,247,234,0.7) 0%, rgba(255,247,234,0) 30%),
      radial-gradient(circle at 85% 80%, rgba(226,172,108,0.6) 0%, rgba(226,172,108,0) 40%),
      linear-gradient(160deg, var(--gold-light) 0%, var(--gold-mid) 55%, var(--gold-deep) 100%);
  }
  .card__bar-top {
    position: absolute; top: 0; left: 0; right: 0;
    height: 17px; background: var(--bar-orange);
  }
  .card__bar-bottom {
    position: absolute; bottom: 0; left: 0; right: 0;
    height: 25px; background: var(--bar-red);
  }

  .quote-mark {
    position: absolute;
    width: 150px;
    height: 95px;
  }
  .quote-mark path { fill: var(--brand-red); }
  .quote-mark--open { left: 67px; top: 100px; }
  .quote-mark--close { left: 962px; top: 842px; }

  .quote {
    position: absolute;
    left: 180px;
    width: 906px;
    top: 196px;
    font-family: "Tinos", "Times New Roman", serif;
    font-weight: 700;
    font-size: 100px;
    line-height: 108px;
    color: var(--ink);
    text-align: center;
  }

  .brand {
    position: absolute;
    left: 34px;
    top: 1010px;
    font-family: "Tinos", "Times New Roman", serif;
    font-weight: 700;
    color: var(--brand-red);
  }
  .brand__name { display: block; font-size: 96px; line-height: 104px; }
  .brand__tagline {
    display: block;
    font-size: 27px;
    letter-spacing: 7px;
    margin-top: 10px;
  }
  .brand__dot {
    position: absolute;
    left: 1003px;
    top: 1028px;
    width: 128px;
    height: 128px;
    border-radius: 50%;
    background: var(--mark-orange);
    box-shadow: 0 0 0 6px var(--white), 0 0 0 9px var(--mark-orange);
  }

  .site-url {
    position: absolute;
    left: 550px;
    top: 1128px;
    font-family: "Arimo", Arial, sans-serif;
    font-size: 28px;
    letter-spacing: 1px;
    color: var(--url-grey);
  }
</style>
</head>
<body>
  <main class="card">
    <div class="card__backdrop" role="img" aria-label="Soft golden bokeh background with glowing sparkles"></div>
    <div class="card__bar-top"></div>

    <svg class="quote-mark quote-mark--open" viewBox="0 0 150 95" aria-hidden="true">
      <path d="M52 0 C22 14 4 38 4 62 C4 82 16 95 32 95 C46 95 58 85 58 70 C58 56 48 46 34 46 C32 46 30 46 28 47 C30 30 42 16 60 8 Z"/>
      <path d="M126 0 C96 14 78 38 78 62 C78 82 90 95 106 95 C120 95 132 85 132 70 C132 56 122 46 108 46 C106 46 104 46 102 47 C104 30 116 16 134 8 Z"/>
    </svg>

    <p class="quote">Ignorance is the curse of God; knowledge is the wing wherewith we fly to heaven</p>

    <svg class="quote-mark quote-mark--close" viewBox="0 0 150 95" aria-hidden="true">
      <path d="M98 95 C128 81 146 57 146 33 C146 13 134 0 118 0 C104 0 92 10 92 25 C92 39 102 49 116 49 C118 49 120 49 122 48 C120 65 108 79 90 87 Z"/>
      <path d="M24 95 C54 81 72 57 72 33 C72 13 60 0 44 0 C30 0 18 10 18 25 C18 39 28 49 42 49 C44 49 46 49 48 48 C46 65 34 79 16 87 Z"/>
    </svg>

    <div class="brand">
      <span class="brand__name">Tornquill</span>
      <span class="brand__tagline">MENTORING SERVICES</span>
    </div>
    <div class="brand__dot" aria-hidden="true"></div>

    <p class="site-url">tornquillmentoring.com</p>

    <div class="card__bar-bottom"></div>
  </main>
</body>
</html>
```